Very dated, simple professional product website needs updating/reskinning of template

Our client currently has a very simple website at www.brightpitch4homes.example that is very, very dated, uses flash, and the template needs to have an updated look for 2014. It needs to look professional, corporate, strong colors, and if using images, actors must have a very well dressed look, etc. Client likes the layout (but not necessarily the colors, etc.) of another similar product site, www.deedcraftkit.example, for example.

The Keystoner product is an online "presentation document builder" that uses up-to-date content for agents to create 20 - 40 page presentations for potential clients. Real estate agents pay $500+ one-time plus $85/year to use the service, so the website look needs to be consistent with a $500+ product. All of the content will stay essentially the same for now: the goal is to simply re-skin the site to make it look modern, ideally through the use of new CSS files and images, and maybe some script. But we do not want to recode the whole thing, just update the template.

The site layout also needs to work with mobile devices, and so the flash has to be removed, but there is still a need to have possibly a slideshow or something to quickly grab the attention of people who visit the site so they can very quickly understand what the product is.

Also, the plan is to cut down on some of the menu buttons and/or rename them to be more compelling. There are pages on the site that can only be viewed after logging in, and we will want to use the template for those secure pages also.

Project Deadline Extended
Reason: My clients have requested that we see if we can get a few more designs to choose between, and to provide them with some time to mull over the current designs.

Project Deadline Extended
Reason: My client has requested that we continue to seek designs.

Industry/Entity Type

Product

```html
<!DOCTYPE html>
<html lang="en">
<head>
<meta charset="utf-8">
<title>Keystoner 4 Real Estate</title>
<link href="https://fonts.googleapis.com/css2?family=Arimo:wght@400;700&family=Roboto+Condensed:wght@400&display=swap" rel="stylesheet">
<style>
:root{
  --ink:#000;
  --text:#555;
  --muted:#777;
  --line:#ccc;
  --paper:#fff;
  --footer-text:#bbb;
  --hero-a:#c9ccd0;
  --hero-b:#8c939c;
  --hero-c:#e8e6e2;
}
*{margin:0;padding:0;box-sizing:border-box}
html,body{width:1200px;height:991px;overflow:hidden;background:var(--paper)}
body{position:relative;font-family:"Arimo",Arial,sans-serif;color:var(--text)}
.abs{position:absolute}
.top-rule{left:0;top:0;width:1200px;height:4px;background:var(--ink)}

.brand{left:162px;top:30px;width:242px}
.brand-name{font-size:40px;color:var(--ink);line-height:1;text-align:center}
.brand-sub{display:flex;align-items:center;gap:10px;margin-top:6px;font-size:17px;color:var(--muted)}
.brand-sub::before,.brand-sub::after{content:"";flex:1;height:1px;background:var(--line)}

.util{top:26px;display:flex;align-items:center;font-size:12px;color:var(--muted)}
.util .ico{width:26px;height:26px;border:1px solid #ddd;border-radius:50%;display:flex;align-items:center;justify-content:center;margin-right:10px}
.util-help{left:532px;font-size:14px;font-weight:700;color:#888}
.util-help .num{color:var(--ink);font-weight:400;font-size:15px;margin-left:6px}
.util-order{left:804px}
.util-order a{color:#333;text-decoration:underline}
.util-members{left:916px}

.nav{left:453px;top:76px;height:28px;display:flex;align-items:center;font-size:12.5px;color:#333}
.nav a{color:#333;text-decoration:none;white-space:nowrap}
.nav .active{background:var(--ink);color:#fff;padding:0 16px;height:28px;line-height:28px}

.hero{left:161px;top:138px;width:878px;height:395px;background:linear-gradient(100deg,var(--hero-c) 0%,var(--hero-a) 35%,var(--hero-b) 55%,var(--hero-a) 75%,var(--hero-c) 100%)}
.caption{background:var(--ink);color:#fff;font-family:"Roboto Condensed",sans-serif;font-size:23px;line-height:34px;padding:0 13px}
.cap1{left:205px;top:299px}
.cap2{left:205px;top:335px;line-height:36px}
.dots{left:554px;top:507px;display:flex;gap:6px}
.dots span{width:14px;height:14px;border-radius:50%;border:1.5px solid var(--ink);background:#fff}
.dots span:first-child{background:transparent}

.welcome{left:162px;top:568px;width:512px}
.welcome h1,.feeds h2{font-family:"Roboto Condensed",sans-serif;font-weight:400;color:var(--ink);font-size:26px}
.welcome .lead{margin-top:20px;font-size:12.3px;font-weight:700;color:#555}
.welcome p.body{margin-top:4px;font-size:11.4px;line-height:17.6px;color:#666}
.divider{left:718px;top:566px;width:1px;height:220px;background:linear-gradient(#fff,#ddd 30%,#ddd 70%,#fff);box-shadow:2px 0 4px rgba(0,0,0,.06)}

.feeds{left:772px;top:566px;width:262px}
.quote{position:relative;margin-top:22px;padding:10px 0 0 9px;font-size:11.4px;line-height:17.6px;color:#666}
.quote .q-open,.quote .q-close{position:absolute;font-family:Georgia,serif;font-size:44px;color:#bbb;line-height:1}
.quote .q-open{left:0;top:-4px}
.quote .q-close{right:0;top:92px}
.quote p{text-indent:28px;padding-right:8px}
.quote cite{display:block;margin-top:18px;font-style:normal;font-weight:700;color:#555}

.footer{left:0;top:821px;width:1200px;height:170px;background:var(--ink);color:var(--footer-text);font-size:11.4px}
.links{list-style:none;top:31px;line-height:19.3px}
.links li::before{content:"";display:inline-block;width:4px;height:4px;border-radius:50%;background:#ccc;margin-right:8px;vertical-align:middle}
.links a{color:var(--footer-text);text-decoration:none}
.links .current a{color:#fff;text-decoration:underline}
.links-main{left:162px}
.links-more{left:365px}
.contact{left:533px;top:33px;line-height:13.6px}
.contact .addr{padding-left:20px;position:relative}
.contact .addr svg{position:absolute;left:0;top:1px}
.contact .phone{margin-top:15px;padding-left:20px;position:relative;color:#fff;font-weight:700;font-size:15px}
.contact .phone svg{position:absolute;left:0;top:2px}
.footer .brand-foot{left:856px;top:31px;width:176px}
.brand-foot .brand-name{color:#fff;font-size:31px}
.brand-foot .brand-sub{font-size:13px;color:#888;margin-top:4px}
.brand-foot .brand-sub::before,.brand-foot .brand-sub::after{background:#666}
.copyright{left:856px;top:104px;font-size:11px;color:#999}
</style>
</head>
<body>
<div class="abs top-rule"></div>

<header>
  <div class="abs brand">
    <div class="brand-name">Keystoner</div>
    <div class="brand-sub">4 Real Estate</div>
  </div>

  <div class="abs util util-help">
    <span class="ico"><svg width="12" height="12" viewBox="0 0 24 24"><path fill="#888" d="M6.6 10.8a15 15 0 0 0 6.6 6.6l2.2-2.2c.3-.3.7-.4 1-.2 1.1.4 2.3.6 3.6.6.6 0 1 .4 1 1V20c0 .6-.4 1-1 1A17 17 0 0 1 3 4c0-.6.4-1 1-1h3.5c.6 0 1 .4 1 1 0 1.3.2 2.5.6 3.6.1.3 0 .7-.2 1z"/></svg></span>
    Help Center - <span class="num">555-014-2270</span>
  </div>
  <div class="abs util util-order">
    <span class="ico"><svg width="13" height="12" viewBox="0 0 24 22"><path fill="none" stroke="#888" stroke-width="2" d="M1 2h4l3 12h12l3-9H7"/><circle cx="10" cy="19" r="2" fill="#888"/><circle cx="18" cy="19" r="2" fill="#888"/></svg></span>
    <a href="#">Order Now</a>
  </div>
  <div class="abs util util-members">
    <span class="ico"><svg width="11" height="12" viewBox="0 0 20 22"><path fill="none" stroke="#888" stroke-width="2.5" d="M5 10V7a5 5 0 0 1 10 0v3"/><rect x="2" y="10" width="16" height="11" rx="2" fill="#888"/></svg></span>
    Members Access
  </div>

  <nav class="abs nav">
    <a class="active" href="#">About Us</a>
    <a href="#" style="margin-left:16px">What is Keystoner</a>
    <a href="#" style="margin-left:32px">Keystoner Demo</a>
    <a href="#" style="margin-left:31px">Peer Reviews</a>
    <a href="#" style="margin-left:31px">F.A.Q</a>
    <a href="#" style="margin-left:28px">Contact Us</a>
  </nav>
</header>

<section>
  <div class="abs hero" role="img" aria-label="Photo of smiling, well dressed business people shaking hands at a meeting table"></div>
  <div class="abs caption cap1">Where Great</div>
  <div class="abs caption cap2">Presentations Begin ...</div>
  <div class="abs dots"><span></span><span></span><span></span><span></span><span></span></div>
</section>

<main>
  <article class="abs welcome">
    <h1>Welcome to Keystoner 4 Real Estate</h1>
    <p class="lead">Your business as an AGENT is selling real estate.</p>
    <p class="body">Our job is in helping you convert more prospects into serious clients so you can do what you do - sell more real estate. We offer you compelling materials to enable you to create your own personal Listing Presentations; Buyer Presentations; Pre-Listing Packages; Unique Open House Hand-Outs; Handling Objection materials; a "keeping Sellers informed" system; Marketing Newsletter plus Presentation Know-How. Quite literally, we provide everything you need to impress your prospects and out-shine your competition. Keystoner was created by veteran B.C. AGENTS for B.C. AGENTS who truly desire success.</p>
  </article>

  <div class="abs divider"></div>

  <aside class="abs feeds">
    <h2>Clien`t Feeds</h2>
    <blockquote class="quote">
      <span class="q-open">&ldquo;</span>
      <p>Success in real estate sales is simple. It's in knowing what to say and how to say it – in a manner that people will heed. Everything else agents do is secondary, yet… it's the secondary stuff most agents focus on, thus, their lack of the success they desire.</p>
      <span class="q-close">&rdquo;</span>
      <cite>-- Dana Whitfield</cite>
    </blockquote>
  </aside>
</main>

<footer class="abs footer">
  <ul class="abs links links-main">
    <li class="current"><a href="#">Home</a></li>
    <li><a href="#">What is Keystoner</a></li>
    <li><a href="#">Keystoner Demo</a></li>
    <li><a href="#">Testimonials</a></li>
    <li><a href="#">Free Presentation Tips</a></li>
    <li><a href="#">F.A.Q.</a></li>
  </ul>
  <ul class="abs links links-more">
    <li><a href="#">Order Keystoner</a></li>
    <li><a href="#">Newsletter</a></li>
    <li><a href="#">Privacy Policy</a></li>
    <li><a href="#">Terms of Use</a></li>
    <li><a href="#">Contact Us</a></li>
  </ul>
  <div class="abs contact">
    <div class="addr">
      <svg width="12" height="16" viewBox="0 0 12 16"><path fill="none" stroke="#bbb" stroke-width="1.5" d="M6 15S1 9 1 6a5 5 0 0 1 10 0c0 3-5 9-5 9z"/><circle cx="6" cy="6" r="1.8" fill="#bbb"/></svg>
      C/o, HARBOURLINE AGENT SUPPORT INC.<br>300 - 42 Cedar Quay North<br>Lakeport, B.C. V0X 9Z9
    </div>
    <div class="phone">
      <svg width="13" height="13" viewBox="0 0 24 24"><path fill="#bbb" d="M6.6 10.8a15 15 0 0 0 6.6 6.6l2.2-2.2c.3-.3.7-.4 1-.2 1.1.4 2.3.6 3.6.6.6 0 1 .4 1 1V20c0 .6-.4 1-1 1A17 17 0 0 1 3 4c0-.6.4-1 1-1h3.5c.6 0 1 .4 1 1 0 1.3.2 2.5.6 3.6.1.3 0 .7-.2 1z"/></svg>
      555.013.8844
    </div>
  </div>
  <div class="abs brand-foot">
    <div class="brand-name">Keystoner</div>
    <div class="brand-sub">4 Real Estate</div>
  </div>
  <div class="abs copyright">Copyright © 2014. All Right Reserved</div>
</footer>
</body>
</html>
```